Web Design Project - Shipping Industry

Goals and Objectives
The objective of the new website is to create a more modern look and feel. The site will also allow for a more effective means of communicating with members while providing the public with information and developments in the local, regional and international shipping industry.
Scope
The website will highlight the history of the organisation inclusive of text and photographs. It will take visitors through the years from beginning to present. Information on the history of the shipping industry will also be included.
It will feature current articles on the organisation, its members and stakeholders in the shipping industry. Member information as well as pertinent details regarding the organisation’s subsidiaries will be documented for the website.
Information as it relates to shipping statistics, case studies, laws and regulations, international treaties and trade documents, shipping terms, careers in shipping, job opportunities, training opportunities, information for shippers including port listing and trade lanes will be main features of the content for the website.
The Association’s community involvement, industry calendar events and related links relevant industry members will also be featured.
Target Market
• The General Public;
• Members of the organization;
• Shipping Industry Stakeholders (local, regional and international);
• Tertiary students conducting research.
• Potential employees
• Potential Business Partners
Best Practice Bench Marketing
The following websites are being looked at:
• Korvel Quayworks - http://www.korvelquayworks.example/ (preferred look)
• Tessaly Maritime Association - http://www.tma-freight.example/ (like image transition on main page)
• Drovna - http://www.drovna.example (professional look)
• PLW - http://www.pelworth.example (preferred color: blue in logo)
• Quillo - http://www.quillo.example/electronics/tv-video-audio/ (preferred look for links page: image + short text below + visit site link)
Expected Result
• 3 - 5 pages which must include: [1] main page [2] standard page [3] links page

```html
<!DOCTYPE html>
<html lang="en">
<head>
<meta charset="utf-8">
<title>Corvane PCS</title>
<link rel="stylesheet" href="https://fonts.googleapis.com/css2?family=PT+Sans:wght@400;700&display=swap">
<style>
:root{
  --sky-top:#6cb2d8;
  --sky-bottom:#e3f2f9;
  --panel:#ffffff;
  --brand:#2f4f9a;
  --brand-dark:#34509a;
  --brand-light:#8fa2d8;
  --text:#7a7a7a;
  --text-dark:#555;
  --rule:#dedede;
  --news-bg:#e9e9e9;
  --field-border:#c9c9c9;
}
*{box-sizing:border-box;margin:0;padding:0}
html,body{width:1145px;height:1200px;overflow:hidden}
body{
  position:relative;
  font-family:"PT Sans",sans-serif;
  background:linear-gradient(180deg,var(--sky-top) 0%,#a9d5ea 45%,var(--sky-bottom) 100%);
  color:var(--text);
}
.abs{position:absolute}
.page{left:73px;top:29px;width:1010px;height:1084px;background:var(--panel);border:1px solid #e6e6e6}
.logo{left:88px;top:52px;font-size:38px;color:var(--brand);letter-spacing:.3px}
.search{left:883px;top:64px;width:185px;height:27px;border:1px solid var(--field-border);border-radius:2px;
  box-shadow:inset 0 1px 2px rgba(0,0,0,.1);font-size:11px;font-style:italic;color:#aaa;padding:6px 9px}
.search svg{position:absolute;right:7px;top:7px}
.header-rule{left:87px;top:108px;width:986px;height:1px;background:var(--rule)}
.nav{left:87px;top:124px;height:38px;display:flex;font-size:14px}
.nav a{color:var(--brand);text-decoration:none;padding:10px 14px 0;margin-right:14px}
.nav a.current{background:linear-gradient(180deg,#7d92cf,#4b66ae);color:#fff;width:74px;padding-left:14px;margin-right:14px}
.nav-bar{left:87px;top:162px;width:986px;height:4px;background:var(--brand-light)}
.locate{left:888px;top:121px;width:180px;height:27px;border-radius:14px;
  background:linear-gradient(180deg,#6c86cc,var(--brand-dark));color:#fff;font-size:14px;
  padding:4px 0 0 24px;box-shadow:0 1px 2px rgba(0,0,0,.3)}
.locate svg{position:absolute;right:24px;top:9px}
.slider{left:87px;top:177px;width:984px;height:284px;border:1px solid #cfcfcf;border-bottom:4px solid #d9d9d9;overflow:hidden}
.slider-photo{position:absolute;inset:0;
  background:linear-gradient(180deg,#8fb3d6 0%,#c9dbe8 40%,#dfe7ec 68%,#5d7c95 80%,#2b4a68 100%)}
.slide-title{left:70px;top:50px;font-size:24px;color:#3a3a3a}
.slide-dash{left:70px;top:86px;width:460px;border-top:2px dashed #555}
.slide-text{left:70px;top:99px;width:480px;font-size:12px;line-height:24px;color:#333}
.slider .arrow{position:absolute;top:122px}
h2{font-weight:400;color:var(--brand);font-size:25px}
.welcome-title{left:88px;top:484px}
.welcome-rule{left:87px;top:527px;width:986px;height:1px;background:var(--rule)}
.welcome-text{left:88px;top:544px;width:667px;font-size:11px;line-height:24px;text-align:justify}
.frame{border:2px solid #d7d7d7;background:#fff;padding:1px}
.frame div{width:100%;height:100%}
.welcome-photo{left:781px;top:486px;width:274px;height:192px}
.about-title{left:88px;top:721px}
.about-rule{left:88px;top:763px;width:664px;height:1px;background:var(--rule)}
.about-text{left:90px;top:778px;width:666px;font-size:11px;line-height:24px;text-align:justify}
.finder{left:88px;top:867px;width:274px;height:243px;background:linear-gradient(90deg,#f1f1f1,#fafafa 70%,#fff)}
.finder label{position:absolute;left:16px;font-size:14px;color:var(--brand)}
.select{position:absolute;left:14px;width:246px;height:27px;border:1px solid var(--field-border);border-radius:2px;background:#fff;
  font-size:11px;font-style:italic;color:#999;padding:6px 9px}
.select svg{position:absolute;right:9px;top:10px}
.submit{position:absolute;left:185px;top:180px;width:79px;height:29px;border-radius:3px;
  background:linear-gradient(180deg,#6580c6,var(--brand-dark));color:#fff;font-size:13px;text-align:center;padding-top:6px}
.thumb{width:171px;height:91px}
.news{left:784px;top:721px;width:265px;height:370px;background:var(--news-bg);border-radius:2px}
.news h3{position:absolute;left:14px;top:14px;font-weight:400;color:var(--brand);font-size:19px}
.news-item{position:absolute;left:9px;width:248px;height:82px;background:#fff;padding:10px 8px 0 21px;
  font-size:11.5px;line-height:19.5px;color:var(--text)}
.news-item b{color:#666}
.news-item svg{position:absolute;left:9px;top:16px}
.news .more{position:absolute;right:14px;top:337px;font-size:12px;color:#888}
.footer-links{left:99px;top:1131px;font-size:12px;color:#555}
.footer-links span{color:#888;margin:0 6px}
.copyright{left:99px;top:1161px;font-size:12px;color:#555}
.social{left:942px;top:1138px;display:flex;gap:13px}
.social span{width:33px;height:33px;border-radius:50%}
.s1{background:radial-gradient(circle at 40% 35%,#6f8fd0,#2d4d93)}
.s2{background:radial-gradient(circle at 40% 35%,#7dd4f0,#2497c9)}
.s3{background:radial-gradient(circle at 40% 35%,#6c8ab8,#274776)}
</style>
</head>
<body>
<div class="abs page"></div>

<div class="abs logo">Corvane PCS</div>
<div class="abs search">Search
  <svg width="12" height="12" viewBox="0 0 12 12"><circle cx="5" cy="5" r="3.5" fill="none" stroke="#aaa" stroke-width="1.4"/><line x1="7.5" y1="7.5" x2="11" y2="11" stroke="#aaa" stroke-width="1.6"/></svg>
</div>
<div class="abs header-rule"></div>

<nav class="abs nav">
  <a class="current" href="#">Home</a>
  <a href="#">About Us</a>
  <a href="#">Sustainabilty</a>
  <a href="#">Latest News</a>
  <a href="#">Careers</a>
  <a href="#">Links</a>
  <a href="#">Contact Us</a>
</nav>
<div class="abs nav-bar"></div>
<div class="abs locate">Locate a Terminal
  <svg width="13" height="10" viewBox="0 0 13 10"><path d="M0 0l6 5-6 5zM6 0l6 5-6 5z" fill="#fff"/></svg>
</div>

<section class="abs slider">
  <div class="slider-photo" role="img" aria-label="Loaded container ship at sea with a city skyline on the horizon"></div>
  <div class="abs slide-title">Excepteur sint occaecat cupidatat proident</div>
  <div class="abs slide-dash"></div>
  <p class="abs slide-text">Duis aute irure dolor in reprehenderit in voluptate velit esse cillum dolore eu fugiat sunt in culpa qui officia deserunt mollit anim</p>
  <svg class="arrow" style="left:16px" width="26" height="38" viewBox="0 0 26 38"><path d="M22 2L5 19l17 17" fill="none" stroke="#222" stroke-width="7"/></svg>
  <svg class="arrow" style="left:940px" width="26" height="38" viewBox="0 0 26 38"><path d="M4 2l17 17L4 36" fill="none" stroke="#222" stroke-width="7"/></svg>
</section>

<h2 class="abs welcome-title">Welcome to our site</h2>
<div class="abs welcome-rule"></div>
<p class="abs welcome-text">Sed ut perspiciatis unde omnis iste natus error sit voluptatem accusantium doloremque laudantium, totam rem aperiam, eaque ipsa quae ab illo inventore veritatis et quasi architecto beatae vitae dicta sunt explicabo. Nemo enim ipsam voluptatem quia voluptas sit aspernatur aut odit aut fugit, sed quia consequuntur magni dolores eos qui ratione voluptatem sequi nesciunt. Neque porro quisquam est, qui dolorem ipsum quia dolor sit amet, consectetur, adipisci velit, sed quia non numquam eius modi tempora incidunt ut labore et dolore magnam aliquam quaerat voluptatem. Ut enim ad minima veniam, quis nostrum exercitationem ullam corporis suscipit laboriosam.</p>
<div class="abs frame welcome-photo"><div role="img" aria-label="Red harbour cranes loading a container ship at the quay" style="background:linear-gradient(180deg,#8fb0dc 0%,#b7c9e2 40%,#b34a3e 65%,#6a6d73 100%)"></div></div>

<h2 class="abs about-title">About us</h2>
<div class="abs about-rule"></div>
<p class="abs about-text">Neque porro quisquam est, qui dolorem ipsum quia dolor sit amet, consectetur, adipisci velit, sed quia non numquam eius modi tempora incidunt ut labore et dolore magnam aliquam quaerat voluptatem. Ut enim ad minima veniam, quis nostrum exercitationem ullam corporis suscipit laboriosam.</p>

<form class="abs finder">
  <label style="top:17px">Select Terminal</label>
  <div class="select" style="top:45px">Select a terminal
    <svg width="14" height="8" viewBox="0 0 14 8"><path d="M0 0h14L7 8z" fill="#999"/></svg></div>
  <label style="top:104px">Select Container</label>
  <div class="select" style="top:132px">Break Bulk
    <svg width="14" height="8" viewBox="0 0 14 8"><path d="M0 0h14L7 8z" fill="#999"/></svg></div>
  <div class="submit">SUBMIT</div>
</form>

<div class="abs frame thumb" style="left:387px;top:877px"><div role="img" aria-label="Cargo ship moored at a dock under a crane" style="background:linear-gradient(180deg,#cfdcec,#8e98a6 60%,#b8ab87)"></div></div>
<div class="abs frame thumb" style="left:578px;top:877px"><div role="img" aria-label="Offshore drilling rig on open blue sea" style="background:linear-gradient(180deg,#7aa4d4,#2f5f9d 55%,#1d4378)"></div></div>
<div class="abs frame thumb" style="left:387px;top:987px"><div role="img" aria-label="Ship hull under construction in a dry dock" style="background:linear-gradient(180deg,#8da2bd,#6a5e58 55%,#8a5d45)"></div></div>
<div class="abs frame thumb" style="left:578px;top:987px"><div role="img" aria-label="Green container ship sailing past a port" style="background:linear-gradient(180deg,#9ec3de,#3f8a7d 55%,#245f6c)"></div></div>

<aside class="abs news">
  <h3>Latest News</h3>
  <div class="news-item" style="top:59px"><svg width="6" height="9" viewBox="0 0 6 9"><path d="M0 0l6 4.5L0 9z" fill="#888"/></svg><b>Tempora incidunt</b> ut labore et dolore magnam aliquam quaerat voluptatem. Ut enim ad minima</div>
  <div class="news-item" style="top:147px"><svg width="6" height="9" viewBox="0 0 6 9"><path d="M0 0l6 4.5L0 9z" fill="#888"/></svg><b>Tempora incidunt</b> ut labore et dolore magnam aliquam quaerat voluptatem. Ut enim ad minima</div>
  <div class="news-item" style="top:236px"><svg width="6" height="9" viewBox="0 0 6 9"><path d="M0 0l6 4.5L0 9z" fill="#888"/></svg><b>Tempora incidunt</b> ut labore et dolore magnam aliquam quaerat voluptatem. Ut enim ad minima</div>
  <div class="more">View more...</div>
</aside>

<footer>
  <div class="abs footer-links">Home<span>|</span>About Us<span>|</span>Sustainabilty<span>|</span>Latest News<span>|</span>Careers<span>|</span>Links<span>|</span>Contact Us<span>|</span>Sitemap</div>
  <div class="abs copyright">Copyright © 2012 www.Corvanepcs.example&nbsp; All rights reserved</div>
  <div class="abs social">
    <span class="s1" role="img" aria-label="Social network link"></span>
    <span class="s2" role="img" aria-label="Social network link"></span>
    <span class="s3" role="img" aria-label="Social network link"></span>
  </div>
</footer>
</body>
</html>
```